Quintel Packaging Business Card

Project Overview
We are seeking a modern, minimalist business card that effectively represents our company while making a bold and lasting impression. The design should reflect trust, professionalism, and innovation, reinforcing our expertise in custom plastic manufacturing for warehouse and distribution centers.

Provided Assets & Specifications
Logo: We will provide our official logo for integration into the design.
Design Files: Photoshop (PSD) files for our printing specifications will be supplied.

Card Size & Material:
Dimensions: 3.5" x 2"
Material: 1/8" Radius Plastic Business Cards with 1/8" Rounded Corners
Clear plastic background—the design should strategically incorporate transparency.
Orientation: The card should be designed in landscape format for a sleek and professional presentation.

Design Requirements:
Logo Prominence
The logo must be the focal point of the card.
Space should be used effectively to draw attention to the logo while maintaining a minimalist layout.

Clear Plastic Integration
The transparent background should create the illusion of blank space, enhancing the modern and high-quality feel.
Avoid any frosted effects—we do not want white areas to appear semi-transparent.

Minimalist & Impactful
Clean, structured, and easy to read at a glance.
Focus on sharp contrast to ensure legibility and visibility.
The design should instill confidence and reflect our role as a leading plastics manufacturer.

Color Palette & Contrast
Primary Colors: Blue, Black, White, and Grey
Use bold black or blue for text and key elements to ensure they stand out against the clear plastic.
Avoid light, pastel, or neon colors that may fade into the plastic background.
No frosted or semi-transparent white—we do not want a cloudy effect.

Typography & Information Hierarchy
Bold, modern typography—clear, professional, and highly legible.
The business card should highlight:
Company Logo (Primary Focus)
Full Name & Title
Phone Number
Email
Website

Brand Representation
The card should reflect our expertise in manufacturing high-quality custom plastics for large-scale packaging and distribution businesses.
Our clients rely on us to enhance their brand presence through custom plastic solutions, and our business cards should reinforce that sense of precision and trust.

Final Considerations
Utilize the clear plastic effectively to differentiate our brand from standard business cards.
Maintain a sleek, professional aesthetic while ensuring all text and elements remain legible.
The design should align with our industry, conveying reliability and innovation.
We look forward to seeing a design that captures our brand identity, maximizes the clear plastic medium, and makes a strong, professional impact on our clients.

```html
<!DOCTYPE html>
<html lang="en">
<head>
<meta charset="utf-8">
<title>Quintel Packaging Business Card</title>
<link href="https://fonts.googleapis.com/css2?family=Montserrat:wght@400;500;700;800&display=swap" rel="stylesheet">
<style>
  :root {
    --stage: #2b2b2b;
    --brand-blue: #0a8ac4;
    --blue-light: #39b5ea;
    --blue-deep: #06618f;
    --ink: #141414;
    --paper: #ffffff;
    --text-light: #f2f2f2;
    --radius: 19px;
  }
  * { box-sizing: border-box; margin: 0; padding: 0; }
  html, body {
    width: 1200px; height: 689px; overflow: hidden;
    background: var(--stage);
    font-family: "Montserrat", sans-serif;
  }
  .canvas {
    position: relative; width: 1200px; height: 689px;
    display: flex; align-items: center; justify-content: center; gap: 40px;
  }
  .card {
    position: relative; width: 540px; height: 309px;
    border-radius: var(--radius); overflow: hidden;
  }
  /* Front */
  .card-front { background: var(--brand-blue); }
  .front-pattern {
    position: absolute; inset: 0;
    background: linear-gradient(120deg, var(--blue-light) 0%, var(--brand-blue) 50%, var(--blue-deep) 100%);
  }
  .front-brand {
    position: absolute; inset: 0;
    display: flex; align-items: center; justify-content: center; gap: 12px;
  }
  .brand-mark {
    width: 26px; height: 26px; background: var(--paper);
  }
  .front-brand .brand-name {
    color: var(--paper); font-weight: 700; font-size: 26px; letter-spacing: 0.5px;
  }
  /* Back */
  .card-back { display: flex; background: var(--ink); }
  .back-brand {
    width: 46%; background: var(--paper);
    border-right: 3px solid var(--brand-blue);
    display: flex; align-items: center; justify-content: center; gap: 10px;
    padding: 0 14px;
  }
  .back-brand .brand-mark { width: 22px; height: 22px; background: var(--brand-blue); }
  .back-brand .brand-name {
    color: var(--ink); font-weight: 700; font-size: 20px; line-height: 1.15;
  }
  .contact {
    flex: 1; padding: 44px 26px 0 30px; color: var(--text-light);
  }
  .contact-name {
    color: var(--brand-blue); font-weight: 800; font-size: 26px; letter-spacing: 0.5px;
    line-height: 1;
  }
  .contact-title { font-size: 13px; margin-top: 6px; }
  .contact-address { font-size: 13px; line-height: 1.45; margin-top: 16px; }
  .contact-list { list-style: none; margin-top: 14px; font-size: 13px; }
  .contact-list li { display: flex; align-items: center; gap: 9px; line-height: 1.7; }
  .contact-list svg { width: 12px; height: 12px; fill: var(--brand-blue); flex: none; }
</style>
</head>
<body>
<main class="canvas">
  <section class="card card-front">
    <div class="front-pattern" role="img" aria-label="Repeating pattern of embossed blue cubes"></div>
    <div class="front-brand">
      <span class="brand-mark"></span>
      <span class="brand-name">Quintel Packaging</span>
    </div>
  </section>

  <section class="card card-back">
    <div class="back-brand">
      <span class="brand-mark"></span>
      <span class="brand-name">Quintel Packaging</span>
    </div>
    <div class="contact">
      <h1 class="contact-name">MARCUS HALE</h1>
      <p class="contact-title">Managing Director</p>
      <p class="contact-address">Your address, City<br>State, Zip 1234</p>
      <ul class="contact-list">
        <li>
          <svg viewBox="0 0 12 12"><path d="M2.5 0.5l2 2.2-1 1.3c.7 1.6 2 2.9 3.5 3.5l1.3-1 2.2 2-1.2 2.5C4.8 10.6 1.4 7.2 0 2.7z"/></svg>
          123 456 789
        </li>
        <li>
          <svg viewBox="0 0 12 12"><path d="M0 2h12v1L6 7 0 3z M0 4.3l6 4 6-4V10H0z"/></svg>
          info@quintelmail.com
        </li>
        <li>
          <svg viewBox="0 0 12 12"><circle cx="6" cy="6" r="5.5"/></svg>
          www.quintelpack.com
        </li>
      </ul>
    </div>
  </section>
</main>
</body>
</html>
```